New Business Card Design

We need a business card design for a new company based in Sydney called "Haven and Hue". This is an online buisness which will have an online store providing imported homewares.
We are looking for something that is different, perhaps even in shape and using the logo that was designed by Pixel Harbor.

Attached document is a basic example I want to see more creative versions.

Target Market(s)

Homewares, Interior Design

Industry/Entity Type

Business

Contact Information for Business Card

Company Logo
Company Name
Industry area
Name
Position
Phone
Email
Website
Motto

Requirements
Must have
• Logo
Nice to have
• Social website logos - Chatterloop, Glimmoraly, Quibbly, Boardlyne, Veltrix+

```html
<!DOCTYPE html>
<html lang="en">
<head>
<meta charset="utf-8">
<title>Haven and Hue – Business Card</title>
<link rel="stylesheet" href="https://fonts.googleapis.com/css2?family=Lato:wght@400;700;900&display=swap">
<style>
  :root {
    --bg: #d3d3d3;
    --ink: #111111;
    --card-dark: #0c0c0c;
    --card-light: #ffffff;
    --gold: #b9822a;
    --text: #2a2a2a;
    --white: #ffffff;
  }
  * { margin: 0; padding: 0; box-sizing: border-box; }
  html, body {
    width: 1200px; height: 1000px; overflow: hidden;
    background: var(--bg);
    font-family: "Lato", sans-serif;
  }
  .canvas { position: relative; width: 1200px; height: 1000px; }

  .card {
    position: absolute;
    width: 640px; height: 370px;
    border-radius: 22px;
    overflow: hidden;
    box-shadow: 0 6px 16px rgba(0,0,0,0.25);
  }

  /* Back of card */
  .card-back { left: 60px; top: 90px; background: var(--card-dark); }
  .social-row {
    position: absolute; top: 30px; right: 36px;
    display: flex; gap: 8px;
  }
  .social-dot {
    width: 26px; height: 26px; border-radius: 50%;
    background: var(--gold);
  }
  .brand-back {
    position: absolute; left: 0; right: 0; top: 140px;
    text-align: center;
    font-weight: 700; font-size: 52px; letter-spacing: 1px;
    color: var(--white);
  }
  .site-back {
    position: absolute; left: 0; right: 0; bottom: 36px;
    text-align: center;
    font-size: 20px; color: var(--white); letter-spacing: 0.5px;
  }
  .site-back .accent { color: var(--gold); }

  /* Front of card */
  .card-front { left: 500px; top: 520px; background: var(--card-light); }
  .brand-front {
    position: absolute; left: 40px; top: 160px; width: 250px;
    text-align: center;
    font-weight: 700; font-size: 34px;
    color: var(--ink);
  }
  .contact {
    position: absolute; left: 330px; top: 48px;
    color: var(--text);
  }
  .contact-name { font-weight: 900; font-size: 28px; color: var(--gold); line-height: 1.1; }
  .contact-role { font-size: 20px; margin-bottom: 18px; }
  .contact-address { font-size: 17px; line-height: 1.3; margin-bottom: 10px; }
  .contact-line {
    display: flex; align-items: center; gap: 10px;
    font-size: 17px; line-height: 1.5;
  }
  .contact-line svg { width: 18px; height: 18px; flex: none; }
  .contact-line.phone { letter-spacing: 2px; }

  .front-band { position: absolute; left: 0; bottom: 0; width: 640px; height: 100px; }
  .site-front {
    position: absolute; right: 40px; bottom: 18px;
    font-size: 18px; color: var(--white); letter-spacing: 0.5px;
  }
</style>
</head>
<body>
<main class="canvas">

  <section class="card card-back" aria-label="Business card back">
    <div class="social-row">
      <span class="social-dot" role="img" aria-label="Chatterloop"></span>
      <span class="social-dot" role="img" aria-label="Quibbly"></span>
      <span class="social-dot" role="img" aria-label="Glimmoraly"></span>
      <span class="social-dot" role="img" aria-label="Boardlyne"></span>
      <span class="social-dot" role="img" aria-label="Veltrix+"></span>
    </div>
    <div class="brand-back">Haven and Hue</div>
    <p class="site-back">www.<span class="accent">havenandhue</span>.com.au</p>
  </section>

  <section class="card card-front" aria-label="Business card front">
    <div class="brand-front">Haven and Hue</div>

    <div class="contact">
      <p class="contact-name">Marcus Ellery</p>
      <p class="contact-role">Director</p>
      <p class="contact-address">Unit 0, Harbour Lane<br>Stillwater 1234 Queensland AU</p>
      <p class="contact-line phone">
        <svg viewBox="0 0 24 24" aria-hidden="true"><path fill="#b9822a" d="M6.6 10.8a15 15 0 0 0 6.6 6.6l2.2-2.2a1 1 0 0 1 1-.25 11.4 11.4 0 0 0 3.6.57 1 1 0 0 1 1 1V20a1 1 0 0 1-1 1A17 17 0 0 1 3 4a1 1 0 0 1 1-1h3.5a1 1 0 0 1 1 1c0 1.25.2 2.45.57 3.6a1 1 0 0 1-.25 1z"/></svg>
        0798765432
      </p>
      <p class="contact-line">
        <svg viewBox="0 0 24 24" aria-hidden="true"><rect x="2" y="5" width="20" height="14" fill="#b9822a"/><path d="M2 5l10 8 10-8" fill="none" stroke="#fff" stroke-width="1.6"/></svg>
        me@havenandhue.com.au
      </p>
    </div>

    <svg class="front-band" viewBox="0 0 640 100" aria-hidden="true">
      <polygon points="0,70 250,70 262,55 560,55 572,40 640,40 640,52 578,52 566,67 268,67 256,82 0,82" fill="var(--gold)"/>
      <polygon points="0,88 258,88 272,64 572,64 584,50 640,50 640,100 0,100" fill="#161212"/>
    </svg>
    <p class="site-front">www.havenandhue.com.au</p>
  </section>

</main>
</body>
</html>
```